Harborview Estates Business Card for Apartment Buildings

Create business cards for resident managers who run apartment buildings. The audience is the public who are searching for apartment rentals, and current residents who live at the apartment building. Key design element will be incorporating the company logo, however, the logo cannot dominate. The building name and manager name are more important than the logo. Current business card design leaves little room for copy, so we may need to reduce the size on the current card to allow for more space for copy.

Target Market(s)

Adults 18-65 years of age, who are looking for an apartment rental, plus current residents who live at our apartment buildings.

Industry/Entity Type

Property Management

Contact Information for Business Card

A major design element will be use of the company logo. Important property and manager contact information must be part of the design. The size of the logo will need to be reduced to make room for building and manager contact copy.

Font styles to use
Sans Serif

Colors
3176b5
000000
959595
ffffff

Requirements
Must have
• 1) Incorporate the company logo.
• 2) Use the company colors (dark blue, black/grey, over white).
• 3) FEATURE THE BUILDING NAME
• 4) FEATURE THE MANAGER NAME
• 5) The company name is less important than BUILDING and MANAGER
• 6) Manager contact information
• **SEE ATTACHED CREATIVE BRIEF**
Nice to have
• 1) Back of card logo watermark
• 2) Ability to write notes on back of carfd
Should not have
• Avoid letting the company logo dominate the card, the building name and manager are more important than the company logo.

```html
<!DOCTYPE html>
<html lang="en">
<head>
<meta charset="utf-8">
<title>Harborview Estates Business Card</title>
<link rel="stylesheet" href="https://fonts.googleapis.com/css2?family=Open+Sans:wght@400;600;700;800&display=swap">
<style>
  :root {
    --brand-blue: #3176b5;
    --ink: #000000;
    --charcoal: #2f2f31;
    --rule-grey: #959595;
    --paper: #ffffff;
    --stage: #e9e7e3;
  }
  * { box-sizing: border-box; margin: 0; padding: 0; }
  html, body { width: 1200px; height: 900px; overflow: hidden; }
  body {
    background: var(--stage);
    font-family: "Open Sans", Arial, sans-serif;
    position: relative;
  }
  .card {
    position: absolute;
    width: 560px;
    height: 320px;
    background: var(--paper);
    overflow: hidden;
    box-shadow: 0 6px 18px rgba(0,0,0,0.18);
  }

  /* Back of card */
  .card-back { left: 70px; top: 110px; }
  .back-panel {
    position: absolute; left: 0; top: 0; bottom: 0; width: 240px;
    background: var(--brand-blue);
  }
  .back-panel-curve {
    position: absolute; left: 40px; top: 20px; width: 380px; height: 380px;
    border-radius: 50%; background: var(--paper);
  }
  .back-name {
    position: absolute; left: 70px; top: 140px;
    font-weight: 800; font-size: 26px; line-height: 1.15;
    color: var(--brand-blue); letter-spacing: 0.5px;
  }
  .notes {
    position: absolute; left: 320px; top: 30px; right: 30px;
    list-style: none;
  }
  .notes li {
    height: 36px;
    border-bottom: 1px solid var(--rule-grey);
  }

  /* Front of card */
  .card-front { left: 570px; top: 470px; }
  .company {
    position: absolute; right: 34px; top: 34px;
    display: flex; align-items: center; gap: 10px;
  }
  .company-dot {
    width: 18px; height: 18px; border-radius: 50%; background: var(--brand-blue);
  }
  .company-name {
    font-weight: 800; font-size: 24px; color: var(--brand-blue);
    letter-spacing: 0.5px; text-transform: uppercase;
  }
  .top-rule {
    position: absolute; left: 250px; right: 34px; top: 86px;
    border-top: 1px solid #d8d8d8;
  }
  .manager {
    position: absolute; left: 34px; top: 118px;
  }
  .manager-name {
    font-weight: 700; font-size: 24px; color: var(--brand-blue);
    letter-spacing: 0.4px; line-height: 1;
  }
  .manager-role {
    font-size: 13px; color: var(--charcoal); margin-top: 4px;
  }
  .name-rule {
    position: absolute; left: 200px; right: 34px; top: 140px;
    border-top: 1px solid #d8d8d8;
  }
  .contacts {
    position: absolute; left: 34px; top: 180px; list-style: none;
  }
  .contacts li {
    display: flex; align-items: center; gap: 8px;
    font-size: 14px; color: var(--ink); line-height: 21px;
  }
  .contacts svg { width: 13px; height: 13px; fill: var(--brand-blue); flex: none; }
  .address {
    position: absolute; right: 34px; top: 156px; text-align: right;
    font-size: 12px; color: var(--ink); line-height: 17px; font-style: normal;
  }
  .band-blue {
    position: absolute; right: 0; bottom: 28px; width: 210px; height: 10px;
    background: var(--brand-blue);
  }
  .band-dark {
    position: absolute; left: 0; right: 0; bottom: 0; height: 28px;
    background: var(--charcoal);
  }
</style>
</head>
<body>

  <section class="card card-back" aria-label="Back of business card">
    <div class="back-panel"></div>
    <div class="back-panel-curve"></div>
    <div class="back-name">HARBORVIEW<br>ESTATES</div>
    <ul class="notes" aria-label="Lines for notes">
      <li></li><li></li><li></li><li></li><li></li><li></li>
    </ul>
  </section>

  <section class="card card-front" aria-label="Front of business card">
    <div class="company">
      <span class="company-dot"></span>
      <span class="company-name">Harborview Estates</span>
    </div>
    <div class="top-rule"></div>

    <div class="manager">
      <h1 class="manager-name">DANIEL WHITAKER</h1>
      <p class="manager-role">Property Manager</p>
    </div>
    <div class="name-rule"></div>

    <ul class="contacts">
      <li>
        <svg viewBox="0 0 16 16" aria-hidden="true"><path d="M2 6c0-2 2-3 6-3s6 1 6 3v1h-3V5.5H5V7H2z M3 8h10l1 5H2z"/></svg>
        555-014-2286
      </li>
      <li>
        <svg viewBox="0 0 16 16" aria-hidden="true"><path d="M4 1h8v4H4z M1 6h14v6h-3v3H4v-3H1z M5 10v4h6v-4z"/></svg>
        555-014-7731
      </li>
      <li>
        <svg viewBox="0 0 16 16" aria-hidden="true"><path d="M1 3h14v10H1z M2 4l6 5 6-5v1L8 10 2 5z" fill-rule="evenodd"/></svg>
        daniel@harborviewestates.us
      </li>
      <li>
        <svg viewBox="0 0 16 16" aria-hidden="true"><circle cx="8" cy="8" r="7"/></svg>
        www.harborviewestates.us
      </li>
    </ul>

    <address class="address">
      2780 Larkspur Valley Road #B210<br>
      Fairhaven, CA 90417
    </address>

    <div class="band-blue"></div>
    <div class="band-dark"></div>
  </section>

</body>
</html>
```